Business Card Design

I am an Event and Wedding Planner in need of an eye catching business card featuring my logo (attached), my contact details, and my company tagline (Making every celebration glow with wonder...) I would like the tagline in font similar the logo's font.
Updates
I have just noticed that my logo has a misspelling so for the final design, I will be uploading a corrected logo as soon as I have it.
My apologies.
Reason: Waiting on a corrected logo...Lantern is misspelled and it should say Weddings not Wedding
The logo has been corrected so now Lantern is spelled correctly and it says Weddings instead of Wedding. Please use Edwardian Script ITC as the font for the tagline so it will match the logo. Thank you for your patience.
Target Market(s)
Engaged couples and people hosting milestone celebrations. 25-50 years old, predominately female
Industry/Entity Type
Business
Contact Information for Business Card
Rosalind Merrow, Event Manager / Owner, Mobile: 0491 868 254, Email: rosalind@velvetlanternco.com.au, www.velvetlanternco.com.au, Making every celebration glow with wonder...

```html
<!DOCTYPE html>
<html lang="en">
<head>
<meta charset="utf-8">
<title>Velvet Lantern – Business Card</title>
<link rel="stylesheet" href="https://fonts.googleapis.com/css2?family=Open+Sans:wght@400;600;700&family=Pinyon+Script&display=swap">
<style>
  :root {
    --stage: #ecebe8;
    --paper: #ffffff;
    --ink: #161616;
    --ink-soft: #4a4a4a;
    --rule: #8a8a8a;
    --accent: #d2303c;
    --band: #0d0d0d;
    --on-band: #f2f2f2;
  }
  * { box-sizing: border-box; margin: 0; padding: 0; }
  html, body {
    width: 1200px; height: 828px; overflow: hidden;
    background: var(--stage);
    font-family: "Open Sans", Arial, sans-serif;
    color: var(--ink);
  }
  .card {
    position: absolute;
    left: 270px;
    width: 660px; height: 377px;
    background: var(--paper);
    box-shadow: 0 6px 18px rgba(0,0,0,.14);
    overflow: hidden;
  }
  .card--front { top: 22px; }
  .card--back  { top: 429px; }

  .brand {
    display: flex; flex-direction: column; align-items: flex-start;
  }
  .brand__mark {
    display: flex; align-items: center; gap: 12px;
  }
  .brand__name {
    font-weight: 600;
    color: var(--ink);
    letter-spacing: .02em;
    white-space: nowrap;
    line-height: 1.1;
  }
  .brand__dot {
    width: 14px; height: 14px; border-radius: 50%;
    background: var(--accent);
    flex: none;
  }
  .brand__rule {
    width: 100%; height: 1px; background: var(--rule);
    margin: 10px 0 6px;
  }
  .brand__tagline {
    font-family: "Pinyon Script", "Edwardian Script ITC", cursive;
    color: var(--ink);
    white-space: nowrap;
    line-height: 1.2;
  }

  .card--front .brand {
    position: absolute; left: 50%; top: 50%;
    transform: translate(-50%, -50%);
    align-items: center;
  }
  .card--front .brand__name { font-size: 40px; }
  .card--front .brand__tagline { font-size: 27px; }

  .card--back .brand {
    position: absolute; left: 44px; top: 66px;
  }
  .card--back .brand__name { font-size: 32px; }
  .card--back .brand__tagline { font-size: 22px; }

  .swoosh { position: absolute; inset: 0; width: 100%; height: 100%; }

  .identity {
    position: absolute; right: 34px; top: 36px;
    text-align: right;
  }
  .identity__name {
    font-size: 15px; font-weight: 700; letter-spacing: .08em;
    text-transform: uppercase;
  }
  .identity__role {
    font-size: 11px; color: var(--ink-soft); margin-top: 2px;
  }
  .identity__address {
    font-size: 11px; color: var(--ink-soft); margin-top: 14px; line-height: 1.5;
  }

  .contacts {
    position: absolute; left: 44px; bottom: 38px;
    list-style: none;
  }
  .contacts__item {
    display: flex; align-items: center; gap: 10px;
    font-size: 12.5px; line-height: 1; margin-top: 9px;
    color: var(--ink);
  }
  .contacts__icon { width: 13px; height: 13px; flex: none; fill: var(--ink); }

  .website {
    position: absolute; right: 30px; bottom: 30px;
    font-size: 13px; letter-spacing: .12em;
    color: var(--on-band);
  }
</style>
</head>
<body>

<section class="card card--front" aria-label="Business card front">
  <div class="brand">
    <div class="brand__mark">
      <span class="brand__name">Velvet Lantern</span>
      <span class="brand__dot"></span>
    </div>
    <span class="brand__rule"></span>
    <p class="brand__tagline">Making every celebration glow with wonder...</p>
  </div>
</section>

<section class="card card--back" aria-label="Business card back">
  <svg class="swoosh" viewBox="0 0 660 377" preserveAspectRatio="none" aria-hidden="true">
    <path fill="var(--accent)" d="M190 377 C400 356 560 280 660 96 L660 377 Z"/>
    <path fill="var(--band)" d="M250 377 C430 358 575 292 660 126 L660 377 Z"/>
  </svg>

  <div class="brand">
    <div class="brand__mark">
      <span class="brand__name">Velvet Lantern</span>
      <span class="brand__dot"></span>
    </div>
    <span class="brand__rule"></span>
    <p class="brand__tagline">Making every celebration glow with wonder...</p>
  </div>

  <div class="identity">
    <p class="identity__name">Rosalind Merrow</p>
    <p class="identity__role">Event Manager / Owner</p>
    <p class="identity__address">Level 4, 27 Harbour Lane<br>Fremont Bay NSW</p>
  </div>

  <ul class="contacts">
    <li class="contacts__item">
      <svg class="contacts__icon" viewBox="0 0 16 16" aria-hidden="true"><path d="M3.6 1 6 3.6 4.6 5.4c.9 2.1 2.8 4 5 5l1.8-1.4L14 11.4 12.6 14C6.8 13.6 2.4 9.2 2 3.4Z"/></svg>
      <span>02 4821 5530</span>
    </li>
    <li class="contacts__item">
      <svg class="contacts__icon" viewBox="0 0 16 16" aria-hidden="true"><path d="M5 1h6a1 1 0 0 1 1 1v12a1 1 0 0 1-1 1H5a1 1 0 0 1-1-1V2a1 1 0 0 1 1-1Zm.5 2v9h5V3Zm2.5 10a.8.8 0 1 0 0 .1Z"/></svg>
      <span>0491 868 254</span>
    </li>
    <li class="contacts__item">
      <svg class="contacts__icon" viewBox="0 0 16 16" aria-hidden="true"><path d="M4 1h6l2 2v3H4Zm-2 6h12a1 1 0 0 1 1 1v5h-3v2H4v-2H1V8a1 1 0 0 1 1-1Zm3 4v3h6v-3Z"/></svg>
      <span>02 4821 5531</span>
    </li>
    <li class="contacts__item">
      <svg class="contacts__icon" viewBox="0 0 16 16" aria-hidden="true"><path d="M1 3h14v10H1Zm1.5 1.3V5l5.5 4 5.5-4v-.7Z"/></svg>
      <span>rosalind@velvetlanternco.com.au</span>
    </li>
  </ul>

  <p class="website">www.velvetlanternco.com.au</p>
</section>

</body>
</html>
```